Need help in designing new business card utilizing our new logo.

BuildMark Solutions works with Construction Business Owners, Managers & IT Professionals to strengthen software usage and increase user productivity.

Our Construction Accounting and Mobile Field Management Software Clients engage with us in the following areas:

New Software Implementations
Software Re-Implementations
Redesigning Software Usage at the User Level
Project Coordination & Management
Continued Software Support

Old tag line:
Weighing Options - Implementing Solutions

www.buildmark-solutions.example

Ridge 4 is a product, but not needed for a new business card.

```html
<!DOCTYPE html>
<html lang="en">
<head>
<meta charset="utf-8">
<title>BuildMark Solutions – Business Card</title>
<link rel="stylesheet" href="https://fonts.googleapis.com/css2?family=Montserrat:wght@400;500;600;700&display=swap">
<style>
  :root {
    --brand-blue: #2b37a6;
    --brand-blue-deep: #1f2a8c;
    --ink: #4a4a4a;
    --muted: #8a8a8a;
    --paper: #ffffff;
    --backdrop: #d9dbe0;
    --on-blue: #e6e8f5;
  }
  * { box-sizing: border-box; margin: 0; padding: 0; }
  html, body { width: 1200px; height: 900px; overflow: hidden; }
  body {
    background: var(--backdrop);
    font-family: "Montserrat", sans-serif;
    display: flex; flex-direction: column; align-items: center; justify-content: center;
    gap: 40px;
  }
  .card {
    width: 700px; height: 400px; position: relative;
    box-shadow: 0 10px 28px rgba(0,0,0,.18);
  }
  /* front */
  .card-front { background: var(--paper); color: var(--ink); padding: 44px 48px; }
  .brand { display: flex; align-items: center; gap: 14px; }
  .brand-square { width: 30px; height: 30px; background: var(--brand-blue); }
  .brand-name { font-size: 30px; font-weight: 600; color: var(--brand-blue); letter-spacing: .5px; }
  .person { margin-top: 38px; }
  .person-name { font-size: 26px; font-weight: 600; color: var(--brand-blue); }
  .person-title { font-size: 16px; color: var(--muted); margin-top: 2px; }
  .divider { position: absolute; left: 48px; right: 48px; top: 196px; height: 2px; background: var(--brand-blue); }
  .contacts { position: absolute; left: 48px; top: 220px; list-style: none; font-size: 15px; line-height: 1.75; }
  .contacts li { display: flex; align-items: center; gap: 10px; }
  .contacts svg { width: 13px; height: 13px; fill: var(--brand-blue); flex: none; }
  .specialty {
    position: absolute; right: 48px; top: 140px; text-align: right;
    font-size: 16px; font-weight: 600; color: var(--brand-blue); line-height: 1.35;
  }
  .address {
    position: absolute; right: 48px; bottom: 44px; text-align: right;
    font-size: 15px; line-height: 1.5; color: var(--ink);
  }
  /* back */
  .card-back {
    background: linear-gradient(135deg, var(--brand-blue) 0%, var(--brand-blue-deep) 100%);
    color: var(--on-blue);
    display: flex; flex-direction: column; justify-content: center; align-items: flex-end;
    padding: 48px 56px; text-align: right;
  }
  .card-back .brand-square { background: var(--on-blue); }
  .card-back .brand-name { color: var(--on-blue); font-size: 36px; }
  .services { list-style: none; margin-top: 40px; font-size: 16px; line-height: 1.65; font-weight: 500; }
</style>
</head>
<body>
  <section class="card card-front">
    <div class="brand">
      <span class="brand-square"></span>
      <span class="brand-name">BuildMark Solutions</span>
    </div>
    <div class="person">
      <p class="person-name">Dana R. Whitfield</p>
      <p class="person-title">Owner</p>
    </div>
    <p class="specialty">Construction Accounting<br>Software Consultants</p>
    <div class="divider"></div>
    <ul class="contacts">
      <li><svg viewBox="0 0 16 16" aria-hidden="true"><path d="M3 1l3 1 1 4-2 1c1 2 2 3 4 4l1-2 4 1 1 3-2 2C7 15 1 9 1 3z"/></svg>800-555-0142 ext.100</li>
      <li><svg viewBox="0 0 16 16" aria-hidden="true"><path d="M4 0h8a1 1 0 011 1v14a1 1 0 01-1 1H4a1 1 0 01-1-1V1a1 1 0 011-1zm1 2v10h6V2zm3 11a1 1 0 100 2 1 1 0 000-2z"/></svg>555-013-4821</li>
      <li><svg viewBox="0 0 16 16" aria-hidden="true"><path d="M1 3h14v10H1zm1 1v1l6 4 6-4V4z"/></svg>dana.whitfield@buildmark-solutions.example</li>
      <li><svg viewBox="0 0 16 16" aria-hidden="true"><circle cx="8" cy="8" r="7"/></svg>www.buildmark-solutions.example</li>
    </ul>
    <p class="address">14B Mercer Street<br>PMB 118 Lakeview Falls<br>NY 12000</p>
  </section>

  <section class="card card-back">
    <div class="brand">
      <span class="brand-square"></span>
      <span class="brand-name">BuildMark Solutions</span>
    </div>
    <ul class="services">
      <li>New Software Implementations | Software Re-Implementations</li>
      <li>Redesigning Software Usage at the User Level</li>
      <li>Project Coordination &amp; Management</li>
      <li>Continued Software Support</li>
    </ul>
  </section>
</body>
</html>
```